Lorvex Tilo medical cannibis cultivation company

tag - Tilo rise
Lorvex Tilo medical cannabis cultivation - logo is selected- can we please see bold examples with our selection. We are mainly dealing with medical companies and professionals. We would like to be stand out in the crowd with our designs. Welcome any and all attempts. Thanks

Target Market(s)

Medical and Professional

Industry/Entity Type

Medical And Science

Font styles to use
Sans Serif

Colors

Designer to choose colors to be used in the design.

Requirements
Must have
• Bright colour and be bold- Love the teal and magenta that is currently on the dark background design.
Nice to have
• shading and the 3D affect- The shadowed appearance.
Should not have
• Anything related to illegal activity or un professional manners

```html
<!DOCTYPE html>
<html lang="en">
<head>
<meta charset="utf-8">
<title>Lorvex Tilo – Business Card</title>
<link href="https://fonts.googleapis.com/css2?family=Marcellus&display=swap" rel="stylesheet">
<style>
  :root {
    --teal: #00aee8;
    --magenta: #9c4f99;
    --white: #ffffff;
    --grey: #8a9199;
    --backdrop: #2a2a2a;
  }
  * { margin: 0; padding: 0; box-sizing: border-box; }
  html, body {
    width: 1125px;
    height: 1200px;
    overflow: hidden;
    background: var(--backdrop);
    font-family: "Marcellus", serif;
  }
  .canvas { position: relative; width: 1125px; height: 1200px; }
  .card {
    position: absolute;
    left: 150px;
    width: 825px;
    height: 471px;
    border-radius: 26px;
    overflow: hidden;
  }
  .card--front { top: 98px; background: var(--teal); color: var(--white); }
  .card--back { top: 631px; background: var(--white); }

  .front-split { position: absolute; inset: 0; }

  .brand-name {
    position: absolute; left: 48px; top: 38px;
    font-size: 56px; line-height: 1; letter-spacing: 0.5px;
  }
  .tagline {
    position: absolute; left: 52px; top: 92px; width: 314px;
    display: flex; align-items: center; gap: 10px;
    font-size: 22px; letter-spacing: 2px; text-transform: uppercase;
  }
  .tagline::before, .tagline::after {
    content: ""; flex: 1; height: 2px; background: currentColor;
  }
  .person-name {
    position: absolute; left: 50px; top: 162px;
    font-size: 34px; letter-spacing: 1px; text-transform: uppercase;
  }
  .person-role {
    position: absolute; left: 51px; top: 200px;
    font-size: 24px; letter-spacing: 1px; text-transform: uppercase;
  }
  .address {
    position: absolute; left: 50px; top: 236px;
    font-size: 19px; line-height: 25px; font-style: normal;
  }
  .contact-list {
    position: absolute; left: 50px; top: 303px;
    list-style: none; font-size: 19px;
  }
  .contact-list li {
    display: flex; align-items: center; gap: 12px; height: 26.5px;
  }
  .contact-list svg { width: 19px; height: 19px; fill: var(--white); flex: none; }

  .back-ring {
    position: absolute; left: 330px; top: 110px;
  }
  .back-name {
    position: absolute; left: 0; right: 0; top: 283px;
    text-align: center; font-size: 54px; line-height: 1;
    color: var(--teal); letter-spacing: 0.5px;
  }
  .back-tagline {
    position: absolute; left: 268px; width: 290px; top: 333px;
    color: var(--grey); font-size: 22px;
  }
</style>
</head>
<body>
<main class="canvas">
  <section class="card card--front" aria-label="Business card front">
    <svg class="front-split" width="825" height="471" viewBox="0 0 825 471" aria-hidden="true">
      <polygon points="578,0 825,0 825,471 511,471" fill="var(--magenta)"/>
    </svg>

    <h1 class="brand-name">LORVEX TILO</h1>
    <p class="tagline">Tilo Rise</p>

    <h2 class="person-name">Marek Olsen</h2>
    <p class="person-role">CEO/Founder</p>

    <address class="address">4210 Larkspur Way<br>Fairview, Oregon 97024</address>

    <ul class="contact-list">
      <li>
        <svg viewBox="0 0 24 24" aria-label="Phone"><path d="M6.6 10.8a15.1 15.1 0 0 0 6.6 6.6l2.2-2.2c.3-.3.7-.4 1-.2 1.1.4 2.3.6 3.6.6.6 0 1 .4 1 1V20c0 .6-.4 1-1 1A17 17 0 0 1 3 4c0-.6.4-1 1-1h3.5c.6 0 1 .4 1 1 0 1.3.2 2.5.6 3.6.1.3 0 .7-.2 1z"/></svg>
        541 208 7736
      </li>
      <li>
        <svg viewBox="0 0 24 24" aria-label="Mobile"><path d="M7 1h10a2 2 0 0 1 2 2v18a2 2 0 0 1-2 2H7a2 2 0 0 1-2-2V3a2 2 0 0 1 2-2zm0 3v14h10V4zm5 15.5a1.2 1.2 0 1 0 0 2.4 1.2 1.2 0 0 0 0-2.4z"/></svg>
        541 390 4412
      </li>
      <li>
        <svg viewBox="0 0 24 24" aria-label="Fax"><path d="M7 2h8l3 3v4H7zM3 10h18a2 2 0 0 1 2 2v7H1v-7a2 2 0 0 1 2-2zm3 4v2h12v-2zM1 20h22v2H1z"/></svg>
        541 775 2069
      </li>
      <li>
        <svg viewBox="0 0 24 24" aria-label="Email"><path d="M2 5h20v14H2zm2 2v.4l8 5.2 8-5.2V7zm0 2.8V17h16V9.8l-8 5.2z"/></svg>
        marek@lorvextilo.com
      </li>
      <li>
        <svg viewBox="0 0 24 24" aria-label="Website"><path d="M12 2a10 10 0 1 0 0 20 10 10 0 0 0 0-20zm-1 17.9A8 8 0 0 1 4.2 10.2L9 15v1a2 2 0 0 0 2 2zm6.9-2.5A2 2 0 0 0 16 16h-1v-3a1 1 0 0 0-1-1H8v-2h2a1 1 0 0 0 1-1V7h2a2 2 0 0 0 2-2v-.4a8 8 0 0 1 2.9 12.8z"/></svg>
        www.lorvextilo.com
      </li>
    </ul>
  </section>

  <section class="card card--back" aria-label="Business card back">
    <svg class="back-ring" width="166" height="166" viewBox="0 0 166 166" aria-hidden="true">
      <circle cx="83" cy="83" r="79" fill="none" stroke="var(--grey)" stroke-width="6"/>
    </svg>
    <h2 class="back-name">LORVEX TILO</h2>
    <p class="tagline back-tagline">Tilo Rise</p>
  </section>
</main>
</body>
</html>
```